Naturopath Practitioner Card Design

I am a naturopath needing a design for a business card mainly to show that I am a naturopath and have some contact details to give to prospective clients. I am open minded about the design and what is on the second side of the card whether it just be some artwork or space for details, appointment times etc. Naturopathy is the practice of natural medicine that uses a holistic approach and incorporates herbal and nutritional medicine.

Industry/Entity Type

Business

Contact Information for Business Card

Tom Rudd NaturopathBHSc (Naturopathy) Member WHPG 0487 925 316 tom.rudd@mailexample.com www.tomruddnaturopathy.example.au

Requirements
Nice to have
• Would prefer some kind of original pattern/art work/logo rather than an image, not fussed if its very simple/basic
• I am open to any colour but think I would prefer a more earthy sandy clay etc type style than the greens that are commonly associated with naturopathy.
Should not have
• Don't really want to have generic stock images on it

```html
<!DOCTYPE html>
<html lang="en">
<head>
<meta charset="utf-8">
<title>Tom Rudd Naturopath – Business Card</title>
<link rel="stylesheet" href="https://fonts.googleapis.com/css2?family=Tinos:wght@400;700&family=Arimo:wght@400;500&display=swap">
<style>
  :root {
    --page-bg: #ece9e4;
    --card-frame: #0d0d0d;
    --metal-light: #d9d9d9;
    --metal-mid: #a9a9a9;
    --metal-dark: #6f6f6f;
    --ink: #161616;
    --emboss-light: rgba(255,255,255,0.55);
    --paper: #f4f4f4;
    --rule: #1e1e1e;
  }
  * { box-sizing: border-box; margin: 0; padding: 0; }
  html, body { width: 1200px; height: 864px; overflow: hidden; }
  body {
    background: var(--page-bg);
    display: flex;
    flex-direction: column;
    align-items: center;
    justify-content: center;
    gap: 44px;
  }
  .card {
    width: 640px;
    height: 366px;
    background: var(--card-frame);
    padding: 12px;
    box-shadow: 0 6px 18px rgba(0,0,0,0.18);
  }
  .card-inner { width: 100%; height: 100%; position: relative; }

  /* Front */
  .card-front .card-inner {
    background:
      radial-gradient(ellipse at 55% 55%, var(--metal-light) 0%, var(--metal-mid) 55%, var(--metal-dark) 100%);
    color: var(--ink);
    text-shadow: 0 1px 0 var(--emboss-light);
    font-family: "Arimo", Arial, sans-serif;
  }
  .identity {
    position: absolute;
    top: 40px;
    left: 0; right: 0;
    text-align: center;
  }
  .practitioner-name {
    font-family: "Tinos", "Times New Roman", serif;
    font-weight: 700;
    font-size: 44px;
    letter-spacing: 1px;
    line-height: 1.05;
  }
  .practitioner-role { font-size: 24px; line-height: 1.2; margin-top: 2px; }
  .practitioner-credentials { font-size: 24px; line-height: 1.2; }
  .divider {
    position: absolute;
    left: 80px; right: 60px;
    top: 190px;
    height: 2px;
    background: var(--rule);
    box-shadow: 0 1px 0 var(--emboss-light);
  }
  .contact {
    position: absolute;
    top: 238px;
    left: 140px;
    font-size: 22px;
    line-height: 1.25;
  }
  .contact-phone { padding-left: 70px; }

  /* Back */
  .card-back .card-inner {
    background: var(--paper);
    color: var(--ink);
    font-family: "Arimo", Arial, sans-serif;
    padding: 28px 34px 0 34px;
  }
  .appointment-title {
    font-family: "Tinos", "Times New Roman", serif;
    font-weight: 700;
    font-size: 40px;
    text-align: center;
    margin-left: 120px;
    margin-bottom: 6px;
  }
  .form-row {
    display: flex;
    align-items: flex-end;
    font-size: 19px;
    height: 40px;
  }
  .form-label { white-space: nowrap; margin-right: 6px; }
  .form-line {
    flex: 1;
    border-bottom: 2px dotted var(--rule);
    margin-bottom: 5px;
  }
  .form-line + .form-label { margin-left: 10px; }
  .days {
    display: flex;
    justify-content: space-between;
    font-size: 18px;
    height: 54px;
    align-items: center;
  }
  .day { display: flex; align-items: center; gap: 4px; }
  .day-box {
    width: 17px; height: 17px;
    border: 1.5px solid var(--rule);
    display: inline-block;
  }
</style>
</head>
<body>

  <section class="card card-front" aria-label="Business card front">
    <div class="card-inner">
      <div class="identity">
        <h1 class="practitioner-name">Tom Rudd</h1>
        <p class="practitioner-role">Naturopath</p>
        <p class="practitioner-credentials">BHSc (Naturopathy) Member WHPG</p>
      </div>
      <div class="divider"></div>
      <div class="contact">
        <p class="contact-phone">0487 925 316</p>
        <p class="contact-email">tom.rudd@mailexample.com</p>
      </div>
    </div>
  </section>

  <section class="card card-back" aria-label="Business card back – appointment">
    <div class="card-inner">
      <h2 class="appointment-title">Appointment</h2>
      <div class="form-row">
        <span class="form-label">For:</span><span class="form-line"></span>
      </div>
      <div class="form-row">
        <span class="form-label">Date:</span><span class="form-line"></span>
        <span class="form-label">Time:</span><span class="form-line"></span>
      </div>
      <div class="days">
        <span class="day"><span class="day-box"></span>MON.</span>
        <span class="day"><span class="day-box"></span>TUE.</span>
        <span class="day"><span class="day-box"></span>WED.</span>
        <span class="day"><span class="day-box"></span>THUR.</span>
        <span class="day"><span class="day-box"></span>FRI.</span>
        <span class="day"><span class="day-box"></span>SAT.</span>
      </div>
      <div class="form-row">
        <span class="form-line"></span>
      </div>
    </div>
  </section>

</body>
</html>
```